Business card design Needed for new logo / Construction business, home extensions and new builds

We need a business card design using our new logo files which i will attach to this project :)

We are a small construction business specialising in home extensions, new builds and property development. We are very ambitious and would appreciate professional and elegant designs for our new business card.

Very serious about using the services on MakerQuarry and recently acquired our new logo from here :)

Please get involved, i will feedback when i can as i am very busy but can respond daily, thanks

Target Market(s)

People that want to build onto their houses, new building developments or adding too their existing property

Industry/Entity Type

Construction

Contact Information for Business Card

Renwick Tolliver Construction, Lionel Ashby (Managing Director), Tel 07822254961, email - info@renwick-tolliver, www.renwick-tolliver.co.uk

Colors

Designer to choose colors to be used in the design.

Requirements
Must have
• I like a deep grey on the back please. A lot of you have provided black from and back, try mixing things up a little. The black looks cool 😎 Thanks

```html
<!DOCTYPE html>
<html lang="en">
<head>
<meta charset="utf-8">
<title>Renwick Tolliver Construction — Business Card</title>
<link href="https://fonts.googleapis.com/css2?family=Montserrat:wght@400;500;700&display=swap" rel="stylesheet">
<style>
  :root {
    --backdrop: #3a3a3a;
    --card-white: #ffffff;
    --card-dark: #161616;
    --gold: #d9a532;
    --gold-soft: #e7bb4e;
    --ink-light: #f2f2f2;
    --shadow: rgba(0, 0, 0, 0.45);
  }
  * { box-sizing: border-box; margin: 0; padding: 0; }
  html, body {
    width: 1200px; height: 689px; overflow: hidden;
    background: var(--backdrop);
    font-family: "Montserrat", Arial, sans-serif;
  }
  .canvas {
    position: relative; width: 1200px; height: 689px;
    display: flex; align-items: center; justify-content: center; gap: 50px;
  }
  .card {
    position: relative; width: 520px; height: 297px;
    border-radius: 18px; overflow: hidden;
    box-shadow: 0 14px 30px var(--shadow);
  }
  /* Front */
  .card-front {
    background: var(--card-white);
    display: flex; align-items: center; justify-content: center;
  }
  .wordmark {
    display: flex; align-items: center; gap: 12px;
    color: var(--gold); font-weight: 700; letter-spacing: 0.08em;
    text-transform: uppercase; text-align: center; line-height: 1.25;
  }
  .wordmark-mark {
    width: 16px; height: 16px; background: var(--gold); flex: none;
  }
  .card-front .wordmark { font-size: 24px; }
  /* Back */
  .card-back { background: var(--card-dark); display: flex; }
  .back-info {
    width: 56%; padding: 34px 0 0 34px; color: var(--ink-light);
  }
  .back-info .wordmark { font-size: 13px; text-align: left; margin-bottom: 26px; }
  .back-info .wordmark-mark { width: 10px; height: 10px; }
  .person-name {
    color: var(--gold); font-weight: 700; font-size: 20px;
    letter-spacing: 0.02em; text-transform: uppercase;
  }
  .person-role { font-size: 12px; margin: 2px 0 16px; }
  .contact-list { list-style: none; font-size: 11.5px; line-height: 1.75; }
  .contact-list li { display: flex; align-items: center; gap: 8px; }
  .contact-list svg { width: 11px; height: 11px; flex: none; fill: var(--gold); }
  .address { font-size: 11.5px; line-height: 1.6; margin-top: 10px; }
  .back-divider { width: 3px; background: var(--gold-soft); }
  .back-brand {
    flex: 1; background: var(--card-white);
    display: flex; align-items: center; justify-content: center; padding: 0 16px;
  }
  .back-brand .wordmark { font-size: 15px; }
</style>
</head>
<body>
<main class="canvas">
  <section class="card card-front" aria-label="Card front">
    <div class="wordmark">
      <span class="wordmark-mark"></span>
      <span>Renwick Tolliver<br>Construction</span>
    </div>
  </section>

  <section class="card card-back" aria-label="Card back">
    <div class="back-info">
      <div class="wordmark">
        <span class="wordmark-mark"></span>
        <span>Renwick Tolliver Construction</span>
      </div>
      <h1 class="person-name">Lionel Ashby</h1>
      <p class="person-role">Managing Director</p>
      <ul class="contact-list">
        <li>
          <svg viewBox="0 0 24 24" aria-hidden="true"><path d="M6.6 10.8a15 15 0 0 0 6.6 6.6l2.2-2.2a1 1 0 0 1 1-.25 11.4 11.4 0 0 0 3.6.57 1 1 0 0 1 1 1V20a1 1 0 0 1-1 1A17 17 0 0 1 3 4a1 1 0 0 1 1-1h3.5a1 1 0 0 1 1 1c0 1.25.2 2.45.57 3.57a1 1 0 0 1-.25 1z"/></svg>
          07822254961
        </li>
        <li>
          <svg viewBox="0 0 24 24" aria-hidden="true"><path d="M2 5h20v14H2zm2 2v.5l8 5 8-5V7l-8 5z"/></svg>
          info@renwick-tolliver.co.uk
        </li>
        <li>
          <svg viewBox="0 0 24 24" aria-hidden="true"><path d="M12 2a10 10 0 1 0 0 20 10 10 0 0 0 0-20zm6.9 6h-3a15 15 0 0 0-1.3-3.9A8 8 0 0 1 18.9 8zM12 4c.8 1.2 1.5 2.5 1.9 4h-3.8c.4-1.5 1.1-2.8 1.9-4zM4.3 14a8 8 0 0 1 0-4h3.4a16 16 0 0 0 0 4zm.8 2h3a15 15 0 0 0 1.3 3.9A8 8 0 0 1 5.1 16zm3-8h-3a8 8 0 0 1 4.3-3.9A15 15 0 0 0 8.1 8zM12 20c-.8-1.2-1.5-2.5-1.9-4h3.8c-.4 1.5-1.1 2.8-1.9 4zm2.3-6H9.7a14 14 0 0 1 0-4h4.6a14 14 0 0 1 0 4zm.3 5.9a15 15 0 0 0 1.3-3.9h3a8 8 0 0 1-4.3 3.9zm1.7-5.9a16 16 0 0 0 0-4h3.4a8 8 0 0 1 0 4z"/></svg>
          www.renwick-tolliver.co.uk
        </li>
      </ul>
      <p class="address">Your address, City<br>State, Zip 1234</p>
    </div>
    <div class="back-divider"></div>
    <div class="back-brand">
      <div class="wordmark">
        <span class="wordmark-mark"></span>
        <span>Renwick Tolliver<br>Construction</span>
      </div>
    </div>
  </section>
</main>
</body>
</html>
```